Kelvor Engineers: Why you should hire us keepsake

New design. Open to plastic cards. We are an engineering firm that designs cell phone towers and commercial buildings. Please check out our website www.kelvorstruct.com for more details. We want people to remember our card and for it to be useful if possible. We want the same look and feel on these cards to be translated to other marketing material we may need such as brochures.

Target Market(s)

Architects, Developers and Telecommunication Carriers

Industry/Entity Type

Engineering

Contact Information for Business Card

Card with our company colors, logo, and innovative design with elements related to our industry.

Font styles to use
Sans Serif

Colors
9bcb3c
abd036
0255a3

Requirements
Must have
• Sleek and hip design
Nice to have
• Bright lime green and navy coloring that pops with an innovative design.
Should not have
• A basic and boring design

```html
<!DOCTYPE html>
<html lang="en">
<head>
<meta charset="utf-8">
<title>Kelvor Engineers – Business Card</title>
<link href="https://fonts.googleapis.com/css2?family=Open+Sans:wght@400;600;800&display=swap" rel="stylesheet">
<style>
  :root {
    --lime: #2fe51a;
    --navy: #132547;
    --navy-line: #0f1f3d;
    --card-white: #f4f6f8;
    --stage: #dfe4ea;
    --text-light: #c9d2e0;
    --icon-green: #3bd42a;
  }
  html, body {
    margin: 0;
    width: 1200px;
    height: 900px;
    overflow: hidden;
    background: var(--stage);
    font-family: "Open Sans", Arial, sans-serif;
  }
  .business-card {
    position: absolute;
    left: 150px;
    top: 194px;
    width: 900px;
    height: 512px;
    border-radius: 22px;
    overflow: hidden;
    background: var(--card-white);
    box-shadow: 0 10px 30px rgba(20, 35, 70, 0.18);
  }
  .card-waves {
    position: absolute;
    inset: 0;
  }
  .brand-name {
    position: absolute;
    left: 42px;
    top: 44px;
    margin: 0;
    font-size: 54px;
    font-weight: 800;
    line-height: 1.05;
    color: var(--lime);
    letter-spacing: -1px;
  }
  .tagline {
    position: absolute;
    right: 42px;
    top: 42px;
    margin: 0;
    font-size: 25px;
    font-weight: 600;
    color: var(--navy);
  }
  .contact-block {
    position: absolute;
    right: 40px;
    top: 308px;
    text-align: right;
    color: var(--text-light);
  }
  .person-name {
    margin: 0 0 28px;
    font-size: 24px;
    font-weight: 600;
  }
  .contact-list {
    list-style: none;
    margin: 0;
    padding: 0;
    font-size: 17px;
    line-height: 27px;
  }
  .contact-list li {
    display: flex;
    justify-content: flex-end;
    align-items: center;
    gap: 8px;
  }
  .contact-icon {
    width: 14px;
    height: 14px;
    flex: none;
  }
</style>
</head>
<body>
  <div class="business-card">
    <svg class="card-waves" viewBox="0 0 900 512" width="900" height="512" aria-hidden="true">
      <!-- navy field -->
      <path d="M150 512 C 300 420, 420 250, 620 226 C 740 212, 840 222, 900 232 L 900 512 Z" fill="var(--navy)"/>
      <!-- green swoosh -->
      <path d="M0 402 C 140 430, 300 380, 470 280 C 620 196, 780 150, 900 162 L 900 198 C 780 178, 640 214, 500 300 C 330 406, 160 460, 0 430 Z" fill="var(--lime)"/>
      <!-- thin navy ribbon -->
      <path d="M70 478 C 240 470, 380 370, 520 282 C 640 210, 760 196, 845 210 C 760 204, 650 226, 540 296 C 400 386, 260 482, 70 478 Z" fill="var(--navy-line)"/>
    </svg>

    <h1 class="brand-name">Kelvor Engineers</h1>
    <p class="tagline">Multi-discipline engineering</p>

    <div class="contact-block">
      <p class="person-name">Dana Holloway Reese</p>
      <ul class="contact-list">
        <li>555.214.0387
          <svg class="contact-icon" viewBox="0 0 16 16"><path d="M3 1 L6 4 L4.5 6 C5.5 8.5 7.5 10.5 10 11.5 L12 10 L15 13 L13 15 C7 14.5 1.5 9 1 3 Z" fill="var(--icon-green)"/></svg>
        </li>
        <li>555.630.9142
          <svg class="contact-icon" viewBox="0 0 16 16"><rect x="4" y="1" width="8" height="14" rx="1.5" fill="none" stroke="var(--icon-green)" stroke-width="1.6"/><circle cx="8" cy="12.5" r="0.9" fill="var(--icon-green)"/></svg>
        </li>
        <li>dreese@kelvorstruct.com
          <svg class="contact-icon" viewBox="0 0 16 16"><rect x="1" y="3.5" width="14" height="9" fill="var(--icon-green)"/><path d="M1 3.5 L8 9 L15 3.5" fill="none" stroke="var(--navy)" stroke-width="1.2"/></svg>
        </li>
        <li>www.kelvorstruct.com
          <svg class="contact-icon" viewBox="0 0 16 16"><circle cx="8" cy="8" r="6.5" fill="none" stroke="var(--icon-green)" stroke-width="1.5"/><ellipse cx="8" cy="8" rx="2.8" ry="6.5" fill="none" stroke="var(--icon-green)" stroke-width="1.2"/><path d="M1.5 8 H14.5" stroke="var(--icon-green)" stroke-width="1.2"/></svg>
        </li>
      </ul>
    </div>
  </div>
</body>
</html>
```